Clear Plastic Card Design

I am looking to have a business card designed from my logo icon. I am looking to match the style of a different business card I have attached in the files.
Looking for a card that is plastic, with layers of transparency in the shape of my logo icon (also attached in the files) - not a circle like the other card. The winning design will incorporate the red icon logo on the front and back and include the charity's name, "Light for the Weary Souls" in the same or similar font, as well as an email and phone number. For now, use the email: email@lightfortheweary-mail.org and the phone number 555-382-7194.
We like how the sample business card has transparency, partial and full opacity layers and a matching color scheme. Files will need to be in vector so that our business card printing company can work with it.
UPDATE:
We've some excellent designs in, thank you everyone! I got an early review from the owner, and he requested a minor redirect to find his perfect design. He wants the design to stand out by NOT being a rectangle. Try instead a circle, square, or best yet - something that falls in the outline of the logo icon, either fully or partially. Thank you, everyone!
Light for the Weary Souls text should be incorporated as well as a phone and email.

```html
<!DOCTYPE html>
<html lang="en">
<head>
<meta charset="utf-8">
<title>Light for the Weary Souls – Business Card</title>
<link href="https://fonts.googleapis.com/css2?family=Questrial&family=Roboto:wght@400&display=swap" rel="stylesheet">
<style>
  :root {
    --page-bg: #e6e0d8;
    --card-frost: rgba(248,246,243,0.55);
    --card-frost-deep: rgba(220,228,238,0.45);
    --ink: #1d1a19;
    --brand-red: #c0202a;
    --band-orange: rgba(226,82,28,0.88);
    --band-red: rgba(184,24,42,0.88);
    --band-deep: rgba(163,18,31,0.9);
    --band-text: rgba(255,235,225,0.8);
  }
  * { margin: 0; padding: 0; box-sizing: border-box; }
  html, body { width: 1200px; height: 969px; overflow: hidden; background: var(--page-bg); }
  .canvas { position: relative; width: 1200px; height: 969px; }
  .card-shadow {
    position: absolute; left: 75px; top: 185px; width: 1050px; height: 598px;
    filter: drop-shadow(0 14px 26px rgba(60,40,30,0.2));
  }
  .card {
    position: relative; width: 100%; height: 100%;
    clip-path: polygon(0 0, calc(100% - 110px) 0, 100% 110px, 100% 100%, 110px 100%, 0 calc(100% - 110px));
    background:
      linear-gradient(160deg, var(--card-frost) 0%, var(--card-frost-deep) 50%, rgba(240,232,222,0.55) 100%),
      rgba(255,255,255,0.35);
    overflow: hidden;
  }
  .card-layer {
    position: absolute; left: 0; top: 0; width: 100%; height: 100%;
    background: linear-gradient(120deg, rgba(255,255,255,0.35) 0%, transparent 40%, rgba(255,255,255,0.2) 70%, transparent 100%);
  }
  .brand {
    position: absolute; left: 376px; top: 130px;
    display: flex; align-items: flex-end; gap: 14px;
  }
  .brand-name {
    font-family: "Questrial", sans-serif; font-size: 36px; line-height: 1.2;
    color: var(--ink); text-align: left; padding-bottom: 22px;
  }
  .brand-mark {
    width: 100px; height: 100px; background: var(--brand-red); margin-bottom: 96px;
    opacity: 0.92;
  }
  .contact-band {
    position: absolute; left: 0; bottom: 0; width: 100%; height: 165px;
    background:
      linear-gradient(175deg, rgba(240,110,40,0.45) 0%, transparent 45%),
      linear-gradient(90deg, var(--band-red) 0%, var(--band-orange) 45%, var(--band-orange) 70%, var(--band-deep) 100%);
    font-family: "Roboto", sans-serif; color: var(--band-text);
  }
  .contact-line {
    position: absolute; left: 0; width: 100%;
    display: flex; justify-content: center; align-items: center; gap: 28px;
    font-size: 22px; line-height: 1;
  }
  .contact-line.phone-line { top: 45px; }
  .contact-line.web-line { top: 94px; }
  .contact-item { display: flex; align-items: center; gap: 10px; white-space: nowrap; }
  .contact-item svg { width: 20px; height: 20px; fill: none; stroke: var(--band-text); stroke-width: 1.8; }
</style>
</head>
<body>
<div class="canvas">
  <div class="card-shadow">
    <div class="card">
      <div class="card-layer"></div>
      <div class="brand">
        <div class="brand-name">Light for the<br>Weary Souls</div>
        <div class="brand-mark"></div>
      </div>
      <div class="contact-band">
        <div class="contact-line phone-line">
          <span class="contact-item">
            <svg viewBox="0 0 20 20"><path d="M5 2l3 4-2 2c1 2.5 3 4.5 5.5 5.5l2-2 4 3-2 3C9 17 3 11 2 5z"/></svg>
            555-382-7194
          </span>
        </div>
        <div class="contact-line web-line">
          <span class="contact-item">
            <svg viewBox="0 0 20 20"><rect x="2" y="4" width="16" height="12"/><path d="M2 4l8 7 8-7"/></svg>
            email@lightfortheweary-mail.org
          </span>
          <span class="contact-item">
            <svg viewBox="0 0 20 20"><circle cx="10" cy="10" r="8"/><path d="M2 10h16M10 2c3 3 3 13 0 16M10 2c-3 3-3 13 0 16"/></svg>
            www.lightforthewearysouls.org
          </span>
        </div>
      </div>
    </div>
  </div>
</div>
</body>
</html>
```